Poster Design Project for an Old-fashioned Ice Cream Parlor

We are an old-fashioned American ice cream company called Pemble's Ice Cream based in the San Francisco Bay Area. We would like a poster design to be put up on display in our parlors. The design should embody the American 1950s retro/vintage look that our company already identifies with, but spruced up with a modern touch. Feel free to be as creative as you like and remix it with your own style! There will be 3 winners and we are hoping for a variety of styles. Each winner will be rewarded with $130. We look forward to seeing your work!
Updates

Hello all,

In reply to some comments, I have uploaded our logo under the 'brief'. Our company was established in 1950. 

Industry/Entity Type

It Company

Requirements
Must have
• the 3 final posters we will select must be formatted to 18x22 inches
designs that incorporate pink, blue, and yellow (our brand colors) will be more likely to win; these colors do not have to be a major part of the artwork
Nice to have
• include the colors pink, blue, and yellow
Should not have
• designs should not be dark in theme

```html
<!DOCTYPE html>
<html lang="en">
<head>
<meta charset="utf-8">
<title>Pemble's Ice Cream Poster</title>
<link href="https://fonts.googleapis.com/css2?family=Rye&family=Lobster&display=swap" rel="stylesheet">
<style>
  :root {
    --brand-blue: #3388cb;
    --brand-pink: #f8c9c8;
    --brand-pink-deep: #f3a9a8;
    --brand-yellow: #fffbd6;
    --paper: #ffffff;
  }
  html, body {
    margin: 0;
    padding: 0;
    width: 1000px;
    height: 1200px;
    overflow: hidden;
    background: var(--paper);
  }
  .poster {
    position: relative;
    width: 1000px;
    height: 1200px;
  }
  .poster__art {
    position: absolute;
    inset: 0;
  }
  .brand-mark {
    position: absolute;
    left: 0;
    width: 1000px;
    top: 465px;
    margin: 0;
    text-align: center;
    font-family: "Rye", serif;
    font-size: 124px;
    line-height: 1;
    color: var(--brand-blue);
  }
  .headline {
    position: absolute;
    left: 0;
    width: 1000px;
    top: 752px;
    margin: 0;
    text-align: center;
    font-family: "Rye", serif;
    font-weight: 400;
    font-size: 68px;
    line-height: 1;
    color: var(--brand-blue);
    -webkit-text-stroke: 8px var(--paper);
    paint-order: stroke fill;
  }
  .tagline {
    position: absolute;
    left: 0;
    width: 1000px;
    top: 846px;
    margin: 0;
    text-align: center;
    font-family: "Lobster", cursive;
    font-size: 36px;
    line-height: 1;
    color: var(--brand-blue);
    -webkit-text-stroke: 5px var(--paper);
    paint-order: stroke fill;
  }
</style>
</head>
<body>
<main class="poster">
  <svg class="poster__art" width="1000" height="1200" viewBox="0 0 1000 1200">
    <defs>
      <linearGradient id="creamWash" x1="0" y1="0" x2="1" y2="0">
        <stop offset="0" stop-color="#fffbd6"/>
        <stop offset="1" stop-color="#fffdf2"/>
      </linearGradient>
      <radialGradient id="swirlWash" cx="0.47" cy="0.55" r="0.7">
        <stop offset="0" stop-color="#f3a9a8"/>
        <stop offset="0.5" stop-color="#f8c9c8"/>
        <stop offset="1" stop-color="#f7c3c2"/>
      </radialGradient>
    </defs>

    <rect class="poster__ground" x="82" y="90" width="835" height="1020" fill="url(#creamWash)"/>

    <rect class="poster__swirl" x="82" y="195" width="835" height="810" fill="url(#swirlWash)" stroke="#ffffff" stroke-width="3"
          role="img" aria-label="Soft pink spiral swirl pattern radiating from the centre"/>

    <g class="banner banner--top">
      <rect x="82" y="153" width="732" height="62" fill="#3388cb" stroke="#ffffff" stroke-width="3"/>
      <polygon points="810,105 915,187 810,270" fill="#3388cb" stroke="#ffffff" stroke-width="3"/>
      <line x1="90" y1="163" x2="806" y2="163" stroke="#ffffff" stroke-width="4" stroke-linecap="round" stroke-dasharray="0 13"/>
      <line x1="90" y1="204" x2="806" y2="204" stroke="#ffffff" stroke-width="4" stroke-linecap="round" stroke-dasharray="0 13"/>
    </g>

    <g class="banner banner--bottom">
      <rect x="82" y="983" width="732" height="62" fill="#3388cb" stroke="#ffffff" stroke-width="3"/>
      <polygon points="810,933 915,1015 810,1097" fill="#3388cb" stroke="#ffffff" stroke-width="3"/>
      <line x1="90" y1="993" x2="806" y2="993" stroke="#ffffff" stroke-width="4" stroke-linecap="round" stroke-dasharray="0 13"/>
      <line x1="90" y1="1034" x2="806" y2="1034" stroke="#ffffff" stroke-width="4" stroke-linecap="round" stroke-dasharray="0 13"/>
    </g>
  </svg>

  <p class="brand-mark">Pemble's</p>

  <h1 class="headline">Pemble's Ice Cream</h1>
  <p class="tagline">“Ice cream from the good old days.”</p>
</main>
</body>
</html>
```